Business card design for Automotive workshop

We need a business card for a new automotive repair and tyre shop called Keelstone Prime Automotive located in New Zealand. We are a clean, modern and fresh workshop and company.

Front needs to feature logo,
my name:
Marlo Fenwicke (director)

Address:
48 Tarn Lane
Whitianga 3510

Phone: 07 594 2713
Mobile: 027 451 9362
Email: office@keelstoneautomotive.example.nz
Website: keelstoneautomotive.example.nz

Back needs to feature an area to write down appointment details, date and time.

Also feature a list of jobs and work we do such as,
Vehicle Servicing
All Mechanical Repairs
Warrant of Fitness
Tyres & Wheel Alignments
Automotive Diagnostics
Automotive Parts & Supplies

```html
<!DOCTYPE html>
<html lang="en">
<head>
<meta charset="utf-8">
<title>Keelstone Prime Automotive – Business Card</title>
<link rel="stylesheet" href="https://fonts.googleapis.com/css2?family=Open+Sans:wght@400;600;700&family=Roboto+Condensed:wght@700&display=swap">
<style>
  :root {
    --backdrop: #d4d5d5;
    --card: #232222;
    --red: #e3202a;
    --white: #ffffff;
    --ink: #2b2b2b;
    --muted: #cfcfcf;
    --rule: #555555;
  }
  * { box-sizing: border-box; margin: 0; padding: 0; }
  html, body { width: 1200px; height: 900px; overflow: hidden; }
  body {
    background: var(--backdrop);
    font-family: "Open Sans", sans-serif;
    position: relative;
  }
  .card {
    position: absolute;
    width: 525px;
    height: 300px;
    background: var(--card);
    color: var(--white);
    box-shadow: 0 6px 14px rgba(0,0,0,.25);
  }
  .card--back { left: 60px; top: 90px; }
  .card--front { left: 615px; top: 500px; }

  .wordmark {
    display: flex;
    align-items: center;
    gap: 10px;
    font-family: "Open Sans", sans-serif;
    font-weight: 700;
    color: var(--red);
    text-transform: uppercase;
    letter-spacing: 1px;
    line-height: 1.05;
  }
  .wordmark__mark {
    width: 14px; height: 14px;
    background: var(--red);
    flex: none;
  }

  /* Back */
  .card--back .wordmark {
    justify-content: center;
    font-size: 19px;
    padding-top: 22px;
  }
  .services {
    text-align: center;
    font-size: 11.5px;
    line-height: 1.45;
    margin-top: 10px;
    color: var(--white);
  }
  .services .dot { color: var(--red); padding: 0 3px; }
  .appointment {
    position: absolute;
    left: 40px; right: 40px; bottom: 26px;
    height: 150px;
    background: var(--white);
    color: var(--ink);
    padding: 12px 22px 0;
  }
  .appointment__title {
    text-align: center;
    color: var(--red);
    font-family: "Roboto Condensed", sans-serif;
    font-weight: 700;
    font-size: 14px;
    letter-spacing: .5px;
    margin-bottom: 12px;
  }
  .appointment__row {
    display: flex;
    align-items: flex-end;
    gap: 6px;
    font-size: 11px;
    height: 32px;
  }
  .appointment__line {
    border-bottom: 1px solid var(--ink);
    height: 1px;
    margin-bottom: 3px;
  }
  .appointment__line--date { flex: 3; }
  .appointment__line--time { flex: 1.3; }
  .appointment__label--time { margin-left: 8px; }

  /* Front */
  .card--front .wordmark {
    position: absolute;
    left: 48px; top: 70px;
    font-size: 24px;
    flex-direction: row;
  }
  .person {
    position: absolute;
    left: 48px; top: 170px;
    text-align: right;
    width: 196px;
  }
  .person__name {
    font-family: "Roboto Condensed", sans-serif;
    font-weight: 700;
    font-size: 20px;
    color: var(--red);
  }
  .person__role { font-size: 11px; margin-top: 2px; }
  .divider {
    position: absolute;
    left: 258px; top: 160px;
    width: 1px; height: 54px;
    background: var(--rule);
  }
  .contacts {
    position: absolute;
    left: 272px; top: 158px;
    list-style: none;
    font-size: 10.5px;
    line-height: 1.4;
  }
  .contacts li { display: flex; align-items: center; gap: 6px; }
  .contacts svg { width: 9px; height: 9px; flex: none; }
  .address {
    position: absolute;
    left: 0; right: 0; bottom: 22px;
    text-align: center;
    font-size: 11px;
  }
</style>
</head>
<body>

<section class="card card--back" aria-label="Card back">
  <div class="wordmark"><span class="wordmark__mark"></span><span>Keelstone Prime Automotive</span></div>
  <p class="services">
    Vehicle Servicing<span class="dot">•</span>All Mechanical Repairs<span class="dot">•</span>Automotive Parts &amp; Supplies<br>
    Tyres &amp; Wheel Alignments<span class="dot">•</span>Automotive Diagnostics<span class="dot">•</span>Warrant of Fitness
  </p>
  <div class="appointment">
    <h2 class="appointment__title">APPOINTMENT</h2>
    <div class="appointment__row"><span>Date</span><span class="appointment__line appointment__line--date"></span><span class="appointment__label--time">Time</span><span class="appointment__line appointment__line--time"></span></div>
    <div class="appointment__row"><span>Date</span><span class="appointment__line appointment__line--date"></span><span class="appointment__label--time">Time</span><span class="appointment__line appointment__line--time"></span></div>
    <div class="appointment__row"><span>Date</span><span class="appointment__line appointment__line--date"></span><span class="appointment__label--time">Time</span><span class="appointment__line appointment__line--time"></span></div>
  </div>
</section>

<section class="card card--front" aria-label="Card front">
  <div class="wordmark"><span class="wordmark__mark"></span><span>Keelstone Prime<br>Automotive</span></div>
  <div class="person">
    <p class="person__name">Marlo Fenwicke</p>
    <p class="person__role">Director</p>
  </div>
  <div class="divider"></div>
  <ul class="contacts">
    <li><svg viewBox="0 0 10 10"><path d="M2 1 L4 1 L4.5 3 L3.3 4 Q4.5 6 6 6.7 L7 5.5 L9 6 L9 8 Q5 9 1.5 5 Q0.5 3 2 1Z" fill="var(--red)"/></svg>07 594 2713</li>
    <li><svg viewBox="0 0 10 10"><rect x="2.5" y="0.5" width="5" height="9" rx="1" fill="none" stroke="var(--red)"/></svg>027 451 9362</li>
    <li><svg viewBox="0 0 10 10"><rect x="0.5" y="1.5" width="9" height="7" fill="none" stroke="var(--red)"/><path d="M0.5 1.5 L5 5.5 L9.5 1.5" fill="none" stroke="var(--red)"/></svg>office@keelstoneautomotive.example.nz</li>
    <li><svg viewBox="0 0 10 10"><circle cx="5" cy="5" r="4.5" fill="none" stroke="var(--red)"/><path d="M0.5 5 H9.5 M5 0.5 Q2 5 5 9.5 M5 0.5 Q8 5 5 9.5" fill="none" stroke="var(--red)" stroke-width=".8"/></svg>keelstoneautomotive.example.nz</li>
  </ul>
  <p class="address">48 Tarn Lane, Whitianga 3510</p>
</section>

</body>
</html>
```